Coastal Learner Bureau business cards

Australian company about to start offering its services. We recruit international students to come to study English, vocational education and postgraduate courses in Australia. We help them find the institution and select the right city they want to come to Australia. We are a young, online oriented and supportive agency. Our clients are between 18 and 35 years old, mainly University students, young professionals or people with work experience. We provide much more information that any other agency offer. We administrate a Facebook group with more than 11.000 members that daily ask questions about general information when coming to Australia, while they are here and even after they leave the country

Target Market(s)

International students from South America, Central America and Europe

Industry/Entity Type

Student

Contact Information for Business Card

Tomas Bilbrea
Managing Director
tomas@kelvarin.com.au
www.kelvoria.com.au
+61 491058264
Melbourne, Australia

Font styles to use
Serif
Sans Serif

Colors

Designer to choose colors to be used in the design.

Requirements
Must have
• Horizontal design
• Standard business card size and shape. If font uses green or yellow colours, they will have to match the ones from the logo
Nice to have
• UPDATE: Use the contents of the green image to design one of the card sides. Use our logo in the background of that side as watermark.
• Passport image, or immigration stamps. A picture of the Yarra River (from Melbourne) would be cool as well.
Should not have
• Non-standard business card size and shape
• Not black as the background colour of any sides as we are not a VIP agency or a hight class service. We are orientes to young people and they like colours, pictures, something attractive.
• Vertical design
• NO YELLOW or BLACK AS THE BACKGROUND COLOUR OF ANY SIDE OF THE BIZ CARD

```html
<!DOCTYPE html>
<html lang="en">
<head>
<meta charset="utf-8">
<title>Coastal Learner Bureau business cards</title>
<link rel="stylesheet" href="https://fonts.googleapis.com/css2?family=Fredoka:wght@600&family=PT+Sans:wght@400;700&display=swap">
<style>
  :root {
    --brand-green: #13613f;
    --brand-green-edge: #1b7048;
    --brand-yellow: #ecc01a;
    --card-white: #f5f5f3;
    --backdrop: #e7e4df;
    --text-light: #ffffff;
  }
  * { box-sizing: border-box; margin: 0; padding: 0; }
  html, body { width: 1200px; height: 886px; overflow: hidden; }
  body {
    background: var(--backdrop);
    display: flex;
    flex-direction: column;
    align-items: center;
    justify-content: center;
    gap: 56px;
    font-family: "PT Sans", sans-serif;
  }
  .card {
    position: relative;
    width: 620px;
    height: 344px;
    border-radius: 22px;
    overflow: hidden;
    box-shadow: 0 10px 28px rgba(0,0,0,.18);
  }
  /* Front side */
  .card--front {
    background: var(--brand-green);
    color: var(--text-light);
  }
  .wordmark {
    font-family: "Fredoka", sans-serif;
    font-weight: 600;
    letter-spacing: 1px;
  }
  .card--front .wordmark {
    position: absolute;
    top: 110px;
    left: 0; right: 0;
    text-align: center;
    font-size: 64px;
    color: var(--text-light);
  }
  .tagline {
    position: absolute;
    left: 0; right: 0;
    bottom: 46px;
    display: flex;
    align-items: center;
    justify-content: center;
    gap: 10px;
    font-size: 15px;
    font-weight: 700;
  }
  .tagline__rule {
    width: 150px;
    height: 1px;
    background: linear-gradient(90deg, rgba(255,255,255,0), rgba(255,255,255,.85));
  }
  .tagline__rule--right {
    background: linear-gradient(90deg, rgba(255,255,255,.85), rgba(255,255,255,0));
  }
  /* Back side */
  .card--back { background: var(--card-white); }
  .side-panel { position: absolute; inset: 0; }
  .card--back .wordmark {
    position: absolute;
    top: 84px;
    right: 70px;
    font-size: 50px;
    color: var(--brand-green);
  }
  .contact {
    position: absolute;
    left: 38px;
    top: 142px;
    color: var(--brand-green);
  }
  .contact__name {
    font-family: "Fredoka", sans-serif;
    font-weight: 600;
    font-size: 24px;
    line-height: 1;
  }
  .contact__role {
    font-size: 15px;
    font-weight: 700;
    margin: 4px 0 16px 12px;
  }
  .contact__list { list-style: none; margin-left: 12px; }
  .contact__item {
    display: flex;
    align-items: center;
    gap: 8px;
    font-size: 14.5px;
    line-height: 21px;
  }
  .contact__icon { width: 13px; height: 13px; flex: none; }
</style>
</head>
<body>

  <section class="card card--front" aria-label="Front of card">
    <div class="wordmark">Kelvoria</div>
    <div class="tagline">
      <span class="tagline__rule"></span>
      <span>Hacemos más por ti!</span>
      <span class="tagline__rule tagline__rule--right"></span>
    </div>
  </section>

  <section class="card card--back" aria-label="Back of card">
    <svg class="side-panel" viewBox="0 0 620 344" aria-hidden="true">
      <path d="M0 0 H230 Q380 150 330 344 H0 Z" fill="var(--brand-yellow)"/>
      <path d="M230 0 Q380 150 330 344" fill="none" stroke="var(--brand-green-edge)" stroke-width="8"/>
    </svg>

    <div class="wordmark">Kelvoria</div>

    <div class="contact">
      <div class="contact__name">Tomas Bilbrea</div>
      <div class="contact__role">Managing Director</div>
      <ul class="contact__list">
        <li class="contact__item">
          <svg class="contact__icon" viewBox="0 0 16 16"><path fill="var(--brand-green)" d="M3 1l3 3-1.5 2a9 9 0 0 0 5.5 5.5L12 10l3 3-2 2C6 15 1 10 1 3z"/></svg>
          <span>+61 491058264</span>
        </li>
        <li class="contact__item">
          <svg class="contact__icon" viewBox="0 0 16 16"><rect x="1" y="3" width="14" height="10" rx="1" fill="var(--brand-green)"/><path d="M1.5 4l6.5 5 6.5-5" fill="none" stroke="var(--brand-yellow)" stroke-width="1.4"/></svg>
          <span>tomas@kelvarin.com.au</span>
        </li>
        <li class="contact__item">
          <svg class="contact__icon" viewBox="0 0 16 16"><circle cx="8" cy="8" r="7" fill="var(--brand-green)"/><path d="M1 8h14M8 1c-3 4-3 10 0 14M8 1c3 4 3 10 0 14" fill="none" stroke="var(--brand-yellow)" stroke-width="1.1"/></svg>
          <span>www.kelvoria.com.au</span>
        </li>
        <li class="contact__item">
          <svg class="contact__icon" viewBox="0 0 16 16"><path fill="var(--brand-green)" d="M8 0a5.5 5.5 0 0 0-5.5 5.5C2.5 10 8 16 8 16s5.5-6 5.5-10.5A5.5 5.5 0 0 0 8 0z"/><circle cx="8" cy="5.5" r="2" fill="var(--brand-yellow)"/></svg>
          <span>Melbourne, Australia</span>
        </li>
      </ul>
    </div>
  </section>

</body>
</html>
```